Corvane Holdings , new business card design

investment firm with corporate clients . need double sided business card , vertical and horizontal options ,logo must be clear. prefer pantone colors only and sharp design. website also www.corvane.ae

Khalid Bin Tarrafi
Managing Director
Tel. +971 4 387 2940
Mobile +971 50 518 2403
khalid@corvane.ae
Q-Span Plaza, officw 18-B07, Warqa Gardens, Dubai

Contact Information for Business Card

Khalid Bin Tarrafi
Managing Director

Font styles to use
Serif

Colors

Designer to choose colors to be used in the design.

```html
<!DOCTYPE html>
<html lang="en">
<head>
<meta charset="utf-8">
<title>Corvane Holdings – Business Card</title>
<link href="https://fonts.googleapis.com/css2?family=Raleway:wght@300;400;600;700&display=swap" rel="stylesheet">
<style>
  :root {
    --navy: #0b2466;
    --white: #ffffff;
    --stage: #e6e7ea;
    --rule: #eceef2;
    --soft-text: #dfe5f3;
  }
  * { margin: 0; padding: 0; box-sizing: border-box; }
  html, body { width: 1200px; height: 900px; overflow: hidden; }
  body {
    background: var(--stage);
    font-family: "Raleway", sans-serif;
    position: relative;
  }
  .card {
    position: absolute;
    width: 640px;
    height: 366px;
    border-radius: 18px;
    overflow: hidden;
    background: var(--white);
    box-shadow: 0 6px 18px rgba(0,0,0,0.12);
  }
  .card--front { left: 80px; top: 60px; }
  .card--back { left: 480px; top: 474px; }

  .rule {
    position: absolute;
    left: 0; right: 0;
    height: 10px;
    background: repeating-linear-gradient(to bottom, var(--rule) 0 1px, transparent 1px 3px);
  }

  /* Front */
  .front__panel {
    position: absolute;
    left: 0; top: 0; bottom: 0;
    width: 322px;
    background: var(--navy);
    color: var(--white);
    padding: 74px 0 0 40px;
  }
  .front__panel::after {
    content: "";
    position: absolute;
    right: -12px; top: 168px;
    border-left: 12px solid var(--navy);
    border-top: 10px solid transparent;
    border-bottom: 10px solid transparent;
  }
  .person__name { font-weight: 700; font-size: 21px; letter-spacing: 0.2px; }
  .person__title { font-weight: 300; font-size: 16px; margin: 4px 0 0 16px; }
  .contact { list-style: none; margin: 20px 0 0 20px; font-size: 15px; font-weight: 400; }
  .contact li { display: flex; align-items: center; gap: 8px; line-height: 23px; }
  .contact svg { width: 12px; height: 12px; flex: none; }
  .address { margin: 22px 0 0 56px; font-size: 15px; font-weight: 400; line-height: 22px; }

  .front__edge {
    position: absolute;
    right: 0; top: 0;
    width: 28px; height: 230px;
    background: var(--navy);
  }
  .front__rule--top { top: 34px; left: 322px; right: 28px; }
  .front__rule--bottom { top: 318px; left: 322px; }

  .brand {
    position: absolute;
    text-transform: uppercase;
    font-weight: 300;
    letter-spacing: 9px;
    line-height: 1.25;
  }
  .front__brand {
    left: 356px; top: 144px;
    color: var(--navy);
    font-size: 28px;
  }

  /* Back */
  .back__box {
    position: absolute;
    left: 140px; top: 100px;
    width: 360px; height: 166px;
    background: var(--navy);
    display: flex;
    align-items: center;
    justify-content: center;
  }
  .back__brand {
    position: static;
    color: var(--white);
    font-size: 30px;
    text-align: center;
  }
  .back__bar { position: absolute; width: 28px; background: var(--navy); }
  .back__bar--left { left: 0; bottom: 0; height: 150px; }
  .back__bar--right { right: 0; top: 0; height: 130px; }
  .back__rule--top { top: 40px; }
  .back__rule--bottom { top: 312px; }
</style>
</head>
<body>

<section class="card card--front" aria-label="Business card front">
  <div class="rule front__rule--top"></div>
  <div class="rule front__rule--bottom"></div>
  <div class="front__edge"></div>

  <div class="front__panel">
    <h1 class="person__name">Khalid Bin Tarrafi</h1>
    <p class="person__title">Managing Director</p>
    <ul class="contact">
      <li>
        <svg viewBox="0 0 12 12" aria-hidden="true"><path d="M3 1 L5 3.5 L4 5 Q5.5 7 7 8 L8.5 7 L11 9 L9.5 11 Q4 10 1 2.5 Z" fill="#fff"/></svg>
        +971 4 387 2940
      </li>
      <li>
        <svg viewBox="0 0 12 12" aria-hidden="true"><rect x="3" y="0.8" width="6" height="10.4" rx="1" fill="none" stroke="#fff" stroke-width="1.2"/></svg>
        +971 50 518 2403
      </li>
      <li>
        <svg viewBox="0 0 12 12" aria-hidden="true"><rect x="0.5" y="2.5" width="11" height="7.5" fill="#fff"/><path d="M0.5 2.5 L6 7 L11.5 2.5" fill="none" stroke="#0b2466" stroke-width="1"/></svg>
        khalid@corvane.ae
      </li>
    </ul>
    <p class="address">Q-Span Plaza, officw 18-B07,<br>Warqa Gardens, Dubai</p>
  </div>

  <p class="brand front__brand">Corvane<br>Holdings</p>
</section>

<section class="card card--back" aria-label="Business card back">
  <div class="rule back__rule--top"></div>
  <div class="rule back__rule--bottom"></div>
  <div class="back__bar back__bar--left"></div>
  <div class="back__bar back__bar--right"></div>
  <div class="back__box">
    <p class="brand back__brand">Corvane<br>Holdings</p>
  </div>
</section>

</body>
</html>
```